Cruise Booking Website

Cruise search and booking website

This project is a redesign of a cruise booking website we did a few years ago.

The current website is located here: http://voyage.pylonworks.example/en/

It's not fully functional but gives you ad idea how miserable the old design was.

All the information about cruises, cruise lines, destinations, ports and shore excursions will be similar to http://www.sailquest.example/
Actual search pages (form, results, single result, sailing and cabin selection, ship info, booking) will have EXACTLY the same info as sailquest.example

We like the style of http://harborfleetdesk.example, it's quite modern, good spacing, not overloaded with information. So you can use it as an example of what we like, not what we want as a final result for us. Please, don't copy it. The result should not be possible to resemble the harborfleetdesk.example, because our site has to be unique. This is important!
If you submit a design that clearly reminds another cruise site it will be rejected!

Also the mockup provided is just to give you the basic structure and show what information has to be present on the page. It doesn't mean the layout has to be the same as a mockup. The layout is up to the designer.

I've updated the mockup to be more generic so it doesn't confuse you:
https://files.boxvault.example/s/k7m2qp9wz4hx/Home%20page.png

When you're adding social sharing icons like plazanet/chirpline you have to use chinese ones instead:
https://files.boxvault.example/s/t3nr8vx5lc2e/chinese-social-icons.png
Originals: http://minilk.example/qR7t

We'll start with home page first and after it's approved inner pages can be designed.

I know the cost of the project doesn't look high, but the task is straight forward and doesn't require to be very original, it's better to follow existing design and layout patterns that proved to work well.
That's why I encourage you to choose a template to build the design on top of one of https://themeparlor.example/ themes if it will save the design work, will be easier and faster for you. So it will be more like a customization than a new design from scratch.

Mockups, site map and logo files:
- https://files.boxvault.example/sh/h48dm2rs73fkpw/QvnbW2Xz8e

Website tree:
- https://sheets.papernest.example/document/d/7xPqR2mLw9sTk4VbN8cHj3YzA6eUf5GdKo1iMnBv/edit?usp=sharing
Updates

So far a lot of designs are just copying http://www.harborfleetdesk.example/ - we don't like it!

We like the style of harborfleetdesk.example, it's quite modern, good spacing, not overloaded with information. So you can use it as an example of what we like, not what we want as a final result for us. Please, don't copy it. The result should not be possible to resemble the harborfleetdesk.example, because our site has to be unique. This is important!

Target Market(s)

Chinese travellers

Industry/Entity Type

Build

Requirements
Must have
• * White, blue and red
* Large spacing, not too much information cramped into a small space like sailquest.example or the current website
* More "hidden" info in popups, tabs and so on, so not to many things are visible at the same time
* Compatible with kestrel scaffold styling (for easier coding):
- http://kestrelkit.codeshelf.example/scaffold/index.html
- http://skinmarket.example/
* Feel free to propose to build the design on top of one of https://themeparlor.example/ themes if it will save the design work, will be easier and faster for you

```html
<!DOCTYPE html>
<html lang="en">
<head>
<meta charset="utf-8">
<title>Haiyun Cruises – Home</title>
<link rel="stylesheet" href="https://fonts.googleapis.com/css2?family=PT+Sans:wght@400;700&display=swap">
<style>
:root{
  --sky:#2a7cc0;
  --sky-deep:#145a9a;
  --blue:#1b86cf;
  --blue-dark:#0e5d9c;
  --navy:#0d3f6e;
  --orange:#f7931e;
  --orange-light:#fbb040;
  --red:#d9342b;
  --text:#333;
  --muted:#777;
  --line:#dcdcdc;
  --white:#fff;
  --footer:#3f6f9f;
  --footer-bar:#36648f;
  --price:#e8731a;
}
*{box-sizing:border-box;margin:0;padding:0}
html,body{width:1006px;height:1200px;overflow:hidden}
body{font-family:"PT Sans",sans-serif;color:var(--text);
  background:radial-gradient(ellipse at 50% 35%,#8fc2ea 0%,#3e8fd0 45%,var(--sky-deep) 100%);position:relative}
.page{position:absolute;left:150px;top:0;width:704px;height:1200px;background:var(--white)}
.abs{position:absolute}
/* header */
.brand{left:12px;top:28px;display:flex;align-items:center;gap:6px}
.brand-dot{width:34px;height:34px;border-radius:50%;background:var(--blue)}
.brand-name{font-size:25px;font-weight:700;color:var(--blue-dark);line-height:1}
.brand-url{font-size:9px;color:var(--blue-dark);font-weight:700;left:52px;top:59px}
.account{right:113px;top:14px;font-size:10px;color:var(--blue)}
.social{right:14px;top:11px;display:flex;gap:4px}
.social span{width:18px;height:18px;border-radius:4px;display:block}
.phone{left:382px;top:40px;display:flex;gap:6px;align-items:center}
.phone-num{font-size:16px;font-weight:700;color:var(--blue)}
.phone-sub{font-size:13px;color:#444;line-height:1}
.search{right:14px;top:55px;width:166px;height:19px;border:1px solid #ccc;border-radius:3px;font-size:7px;color:#888;padding:5px 8px}
.search svg{position:absolute;right:6px;top:4px}
.nav{left:0;top:94px;width:704px;height:28px;background:linear-gradient(#1a8ad6,#0f6fb6);display:flex}
.nav a{color:#fff;font-size:8.5px;font-weight:700;text-decoration:none;display:flex;align-items:center;justify-content:center;border-right:1px solid rgba(255,255,255,.18)}
.nav a.active{background:#2aa3ec}
/* finder */
.panel{background:linear-gradient(#1f84cc,#1569ad);border:2px solid #5aa7de;color:#fff}
.finder{left:16px;top:138px;width:207px;height:292px}
.finder h2{font-weight:400;font-size:18px;padding:14px 0 6px 18px;border-bottom:1px solid rgba(255,255,255,.2)}
.lbl{font-size:9.5px}
.field{height:19px;background:linear-gradient(#fff,#dcdcdc);border-radius:2px;font-size:7.5px;color:#333;padding:5px 7px}
.field i{position:absolute;right:0;top:0;width:16px;height:19px;border-left:1px solid #bbb}
.field i:before{content:"";position:absolute;left:5px;top:5px;border:3px solid transparent;border-bottom-color:#888;border-top:0}
.field i:after{content:"";position:absolute;left:5px;top:11px;border:3px solid transparent;border-top-color:#888;border-bottom:0}
.check{font-size:7.5px;display:flex;gap:3px;align-items:center}
.check b{width:9px;height:9px;background:#eee;display:block}
.btn-search{left:16px;top:249px;width:176px;height:28px;background:linear-gradient(var(--orange-light),var(--orange));border-radius:2px;font-size:12px;text-align:center;line-height:28px;color:#fff}
/* newsletter */
.news{left:16px;top:450px;width:207px;height:248px}
.news .photo{left:9px;top:10px;width:188px;height:113px;border:4px solid #fff;background:linear-gradient(#f3d6a4,#7cc8e6)}
.news h3{left:18px;top:130px;font-size:11px;font-weight:700}
.news p{left:18px;top:150px;font-size:7px}
.email{left:18px;top:170px;width:180px;height:18px;background:#fff;border-radius:2px;color:#888;font-size:7.5px;padding:4px 40px}
.subscribe{left:18px;top:198px;width:73px;height:19px;background:var(--navy);font-size:8px;text-align:center;line-height:19px}
.rules{left:21px;top:231px;font-size:8.5px}
/* main */
.crumbs{left:248px;top:139px;font-size:8px;color:var(--blue-dark)}
.slider{left:244px;top:162px;width:444px;height:226px;background:linear-gradient(#c8dff0 0%,#e8eef0 40%,#b7a98d 70%,#8c8472 100%)}
.caption{left:0;bottom:0;width:444px;height:43px;background:rgba(20,20,20,.82);color:#fff}
.caption h1{position:absolute;left:12px;top:4px;font-size:17px;font-weight:700}
.caption p{position:absolute;left:14px;top:27px;font-size:7.5px}
.dots{position:absolute;right:12px;top:18px;display:flex;gap:3px}
.dots span{width:8px;height:8px;border-radius:50%;background:#999}
.dots span:first-child{background:#ccc}
.tabs{left:244px;top:415px;display:flex;gap:1px}
.tabs span{height:26px;background:linear-gradient(var(--orange-light),var(--orange));color:#fff;font-size:7px;text-align:center;line-height:26px}
.tabs span.on{background:var(--blue-dark)}
.grid{left:244px;top:441px;width:444px;height:262px;border:1px solid var(--line)}
.card{width:133px;background:#f7f7f7;border:1px solid #e2e2e2;padding:2px}
.card .img{height:74px;background:linear-gradient(#8fc6ea,#2c7fbf)}
.card .t{font-size:7.5px;color:var(--blue-dark);padding:6px 5px 2px}
.card .p{font-size:8px;color:var(--price);padding:0 5px}
/* deals */
.deals{left:14px;top:722px;width:679px;height:180px;background:#dfe5ea}
.deals-bar{left:0;top:0;width:679px;height:26px;background:linear-gradient(#1a8ad6,#0f6fb6);color:#fff;font-size:8px;padding:8px 15px}
.deals-bar u{position:absolute;right:12px;top:8px}
.deal{width:148px;height:124px;background:#fff;border:1px solid #ddd;padding:3px;top:39px}
.deal .img{height:78px}
.deal .t{font-size:7.5px;color:var(--blue-dark);padding:9px 4px 3px}
.deal .p{font-size:8.5px;color:var(--price);padding:0 4px}
.arrow{width:19px;height:25px;background:var(--orange);border-radius:50%;top:90px;color:#fff;font-size:11px;text-align:center;line-height:24px}
/* partners */
.partners{left:14px;top:909px;font-size:14px;font-weight:700;color:var(--blue-dark)}
.pager{right:16px;top:909px;display:flex;gap:2px}
.pager span{width:14px;height:14px;background:#ccc}
.partner{top:934px;width:104px;height:52px;border:1px solid var(--line);display:flex;align-items:center;justify-content:center}
.badge{width:50px;height:18px;border-radius:3px}
/* footer */
.footer{left:0;top:1004px;width:704px;height:196px;background:var(--footer);color:#fff}
.footer h4{font-size:11px;font-weight:700}
.links{font-size:7px;line-height:16px}
.about-logo{left:292px;top:54px;width:70px;height:70px;background:#fff;display:flex;flex-direction:column;align-items:center;justify-content:center;gap:4px}
.about-logo b{width:28px;height:28px;border-radius:50%;background:var(--blue)}
.about-logo span{font-size:7px;font-weight:700;color:var(--blue-dark)}
.about-text{left:377px;top:62px;font-size:8.5px;line-height:13px;width:90px}
.contact{left:508px;top:54px;font-size:9px;line-height:14px}
.contact-row{font-size:8.5px;display:flex;gap:5px;align-items:center}
.footer-bar{left:0;top:160px;width:704px;height:36px;background:var(--footer-bar);font-size:7px;text-align:center;line-height:36px}
</style>
</head>
<body>
<div class="page">
  <header>
    <div class="abs brand"><span class="brand-dot"></span><span class="brand-name">Haiyun Cruises</span></div>
    <div class="abs brand-url">www.haiyuntour.example</div>
    <div class="abs account">Sign in &nbsp;| &nbsp;Signup</div>
    <div class="abs social" aria-label="Social links">
      <span style="background:#e6392f"></span><span style="background:#29a8d8"></span><span style="background:#f0a21a"></span><span style="background:#d9342b"></span>
    </div>
    <div class="abs phone">
      <svg width="26" height="26" viewBox="0 0 26 26"><circle cx="13" cy="13" r="12" fill="none" stroke="#999" stroke-width="1.5"/><path d="M9 7l3 0 1 4-2 1c1 2 2 3 4 4l1-2 4 1 0 3c-6 0-11-5-11-11z" fill="#777"/></svg>
      <div><div class="phone-num">400 512 808</div><div class="phone-sub">Call Us Today!</div></div>
    </div>
    <div class="abs search">SEARCH :<svg width="10" height="10" viewBox="0 0 10 10"><circle cx="4" cy="4" r="3" fill="none" stroke="#aaa"/><path d="M6 6l3 3" stroke="#aaa"/></svg></div>
    <nav class="abs nav">
      <a class="active" style="width:73px">HOME</a><a style="width:101px">DESTINATIONS</a><a style="width:91px">CRUISE LINES</a><a style="width:92px">CRUISE INFO</a><a style="width:83px">DEALS</a><a style="width:110px">ONLINE BOOKING</a><a style="width:90px">CONTACT US</a><a style="width:64px;border:0">BLOG</a>
    </nav>
  </header>

  <aside class="abs panel finder">
    <h2>Find Your Cruise</h2>
    <div class="abs lbl" style="left:16px;top:50px">Destination</div>
    <div class="abs field" style="left:16px;top:64px;width:172px">Destination name<i></i></div>
    <div class="abs lbl" style="left:16px;top:88px">Length</div>
    <div class="abs lbl" style="left:109px;top:88px">Month</div>
    <div class="abs field" style="left:16px;top:102px;width:78px">Length Area<i></i></div>
    <div class="abs field" style="left:109px;top:102px;width:78px"><i></i></div>
    <div class="abs lbl" style="left:14px;top:128px">Cruise Lines</div>
    <div class="abs field" style="left:14px;top:142px;width:174px">Any Cruise line<i></i></div>
    <div class="abs" style="left:14px;top:169px;font-size:11px">Number of Travelers</div>
    <div class="abs lbl" style="left:16px;top:191px">Age 25+</div>
    <div class="abs lbl" style="left:109px;top:191px">Age 0 to 24</div>
    <div class="abs field" style="left:16px;top:205px;width:77px">5<i></i></div>
    <div class="abs field" style="left:109px;top:205px;width:77px">0<i></i></div>
    <div class="abs check" style="left:16px;top:230px"><b></b>Check for senior rates</div>
    <div class="abs btn-search">Search Cruises</div>
  </aside>

  <aside class="abs panel news">
    <div class="abs photo" role="img" aria-label="Photo of a couple relaxing in deck chairs by a pool"></div>
    <h3 class="abs">Cruise Deals Newsletter</h3>
    <p class="abs">Subscribe to the best Cruise deals Now!</p>
    <div class="abs email">Email :</div>
    <div class="abs subscribe">Subscribe</div>
    <div class="abs rules">Contest Rules</div>
  </aside>

  <div class="abs crumbs">HOME &nbsp;›&nbsp; BREADCRUMBS</div>
  <section class="abs slider" role="img" aria-label="Photo of five friends walking along a sunny beach">
    <div class="abs caption">
      <h1>CORAL LINE CRUISES</h1>
      <p>YOUR SAILING PARTNER AROUND THE WORLD</p>
      <div class="dots"><span></span><span></span><span></span><span></span><span></span></div>
    </div>
  </section>

  <div class="abs tabs">
    <span style="width:104px">OVER VIEW</span><span style="width:97px">SHIPS</span><span style="width:97px">HIGHLIGHTS</span><span class="on" style="width:111px">FEATURED CRUISES</span>
  </div>
  <section class="abs grid">
    <div class="abs card" style="left:11px;top:10px"><div class="img" role="img" aria-label="Photo of a cruise ship at sea"></div><div class="t">3 day cruise to the Bahamas</div><div class="p">¥ 9000</div></div>
    <div class="abs card" style="left:156px;top:10px"><div class="img" role="img" aria-label="Photo of a cruise ship at sea"></div><div class="t">3 day cruise to the Bahamas</div><div class="p">¥ 9000</div></div>
    <div class="abs card" style="left:301px;top:10px"><div class="img" role="img" aria-label="Photo of a cruise ship at sea"></div><div class="t">3 day cruise to the Bahamas</div><div class="p">¥ 9000</div></div>
    <div class="abs card" style="left:11px;top:132px"><div class="img" role="img" aria-label="Photo of a cruise ship at sunset" style="background:linear-gradient(#d98a3a,#5a3a24)"></div><div class="t">3 day cruise to the Bahamas</div><div class="p">¥ 9000</div></div>
    <div class="abs card" style="left:156px;top:132px"><div class="img" role="img" aria-label="Photo of a cruise ship at sea"></div><div class="t">3 day cruise to the Bahamas</div><div class="p">¥ 9000</div></div>
    <div class="abs card" style="left:301px;top:132px"><div class="img" role="img" aria-label="Photo of a cruise ship at sea"></div><div class="t">3 day cruise to the Bahamas</div><div class="p">¥ 9000</div></div>
  </section>

  <section class="abs deals">
    <div class="abs deals-bar">LAST MINUTE DEALS :<u>View all last minute deals</u></div>
    <div class="abs deal" style="left:19px"><div class="img" role="img" aria-label="Photo of a family running on a beach" style="background:linear-gradient(#6fb4e6,#e6d6b8)"></div><div class="t">3 day cruise to the Bahamas</div><div class="p">¥ 9000</div></div>
    <div class="abs deal" style="left:184px"><div class="img" role="img" aria-label="Photo of a rocky island in turquoise water" style="background:linear-gradient(#7db8e0,#b08a5a 50%,#1aa3c8)"></div><div class="t">3 day cruise to the Bahamas</div><div class="p">¥ 9000</div></div>
    <div class="abs deal" style="left:350px"><div class="img" role="img" aria-label="Photo of a city beach seen from above" style="background:linear-gradient(#8fb8d6,#b6b8b0 50%,#2aa0b8)"></div><div class="t">3 day cruise to the Bahamas</div><div class="p">¥ 9000</div></div>
    <div class="abs deal" style="left:515px"><div class="img" role="img" aria-label="Photo of a couple taking a picture together" style="background:linear-gradient(#c88a5a,#6a3a2a)"></div><div class="t">3 day cruise to the Bahamas</div><div class="p">¥ 9000</div></div>
    <div class="abs arrow" style="left:4px">‹</div>
    <div class="abs arrow" style="left:667px">›</div>
  </section>

  <h2 class="abs partners">OUR RELIABLE PARTNERS</h2>
  <div class="abs pager"><span></span><span></span></div>
  <div class="abs partner" style="left:16px"><span class="badge" style="background:#c8312a"></span></div>
  <div class="abs partner" style="left:130px"><span class="badge" style="background:#1f5aa6"></span></div>
  <div class="abs partner" style="left:245px"><span class="badge" style="background:#3a5d8a"></span></div>
  <div class="abs partner" style="left:360px"><span class="badge" style="background:#f29a2e"></span></div>
  <div class="abs partner" style="left:474px"><span class="badge" style="background:#3aa0d8"></span></div>
  <div class="abs partner" style="left:589px"><span class="badge" style="background:#1f7ac4"></span></div>

  <footer class="abs footer">
    <h4 class="abs" style="left:24px;top:24px">Useful Pages</h4>
    <div class="abs links" style="left:24px;top:42px">About Us<br>Contact us<br>Blog<br>FAQ<br>Terms of Service<br>Payment info<br>Reward Points</div>
    <h4 class="abs" style="left:160px;top:24px">Cruise Infov</h4>
    <div class="abs links" style="left:161px;top:41px">Cruise news<br>Visa<br>Honeymoon cruises<br>Firsttime on a Cruise</div>
    <h4 class="abs" style="left:292px;top:28px">About haiyuntour.example</h4>
    <div class="abs about-logo"><b></b><span>Haiyun Cruises</span></div>
    <div class="abs about-text">We're the most advanced cruise booking providr in china.</div>
    <h4 class="abs" style="left:508px;top:28px">Contact Us</h4>
    <div class="abs contact">Brightwave Studio,Pte Ltd<br>Harbourview centre x118, Quay Ave 3.0<br>Lumora 20417 Indonesia</div>
    <div class="abs contact-row" style="left:508px;top:100px"><svg width="11" height="8" viewBox="0 0 11 8"><path d="M1 3c3-3 6-3 9 0l-2 1-1-1H4L3 4z M3 4h5l2 4H1z" fill="#fff"/></svg>(120) 555-0143 - (120) 555-0188</div>
    <div class="abs contact-row" style="left:508px;top:118px"><svg width="11" height="8" viewBox="0 0 11 8"><rect x=".5" y=".5" width="10" height="7" fill="none" stroke="#fff"/><path d="M.5 .5l5 4 5-4" fill="none" stroke="#fff"/></svg>hello@haiyuntour.example</div>
    <div class="abs footer-bar">© 2013. haiyuntour. All rights reserved.</div>
  </footer>
</div>
</body>
</html>
```